Modern Medical Optometry Website

We need mordern, Patient friendly website. Easy to navigate and enhance our advance medical technology and excellent patient care.
1. HOME PAGE
2. OUR TEAM PAGE
3. EYECARE PAGE - VISION SERVICES, EYE EXAMS, KERATOCONUS CENTER, GLAUCOMA , DIABITES, MELORIDEX EXAM, DIGITAL RETINAL, OCT.
4. MYOPIA CONTROL CLINIC
5. DRY EYE CLINIC
6. EYEWEAR
7. PATIENT CENTER - BLOG
7. CONTACT US
This is our current website www.brivaloka.com
and We want to add more content and a cleaner design like these website
http://tarnwickfolvendale.com/
https://www.qmvorlu.com/

```html
<!DOCTYPE html>
<html lang="en">
<head>
<meta charset="utf-8">
<title>Myopia Control Clinic – Lumora Optometry</title>
<link href="https://fonts.googleapis.com/css2?family=Raleway:wght@300;400;500;600;700&display=swap" rel="stylesheet">
<style>
:root{
  --teal:#1691b3;
  --teal-dark:#0f7f9e;
  --yellow:#fbe564;
  --grey-band:#efefef;
  --ink:#2b2b2b;
  --body:#8a8a8a;
  --white:#ffffff;
  --dark-btn:#2e2e2e;
}
*{box-sizing:border-box;margin:0;padding:0}
html,body{width:1200px;height:3229px;overflow:hidden}
body{font-family:'Raleway',sans-serif;color:var(--ink);background:var(--white);position:relative}
.abs{position:absolute}

/* top bar */
.topbar{top:0;left:0;width:1200px;height:52px;background:var(--teal)}
.topbar .cell{position:absolute;top:0;height:52px;border-left:1px solid rgba(255,255,255,.25);display:flex;align-items:center;justify-content:center;color:var(--white);font-size:15px;font-weight:500;gap:12px}
.topbar .social{width:52px}
.topbar .dot{width:9px;height:9px;border-radius:50%;background:var(--yellow)}

/* header */
.logo-box{top:21px;left:77px;width:109px;height:142px;background:var(--white);box-shadow:0 1px 4px rgba(0,0,0,.08);display:flex;flex-direction:column;align-items:center;justify-content:center;gap:10px}
.logo-box .sq{width:56px;height:56px;background:var(--yellow)}
.logo-box .name{font-size:15px;font-weight:400;color:#555;text-align:center;line-height:1.1}
.nav{top:108px;left:221px;display:flex;gap:0;font-size:16px;font-weight:400;color:#8b8b8b;text-transform:uppercase}
.nav span{margin-right:36px}
.nav .home{color:#555;font-weight:500}
.nav .active{color:var(--teal)}
.search{top:108px;left:1102px}

/* title */
.title-band{top:188px;left:0;width:1200px;height:134px;background:var(--grey-band);display:flex;align-items:center;justify-content:center}
.title-band h1{color:var(--teal);font-size:36px;font-weight:700;letter-spacing:.3px}

/* intro */
.intro{top:362px;left:79px;width:1045px}
.intro h2{font-size:37px;font-weight:400;color:#333;margin-bottom:44px}
.intro p{font-size:14px;line-height:26px;color:var(--body);margin-bottom:26px;font-weight:400}
.intro strong{color:#111;font-weight:600}

/* feature grid */
.tile{position:absolute}
.tile h3{font-size:31px;font-weight:700;margin-bottom:14px}
.tile p{font-size:14px;line-height:26px;font-weight:400}
.tile.teal{background:var(--teal);color:var(--white)}
.tile.yellow{background:var(--yellow);color:#333}
.photo-optician{top:825px;left:0;width:600px;height:531px;background:linear-gradient(100deg,#ececec 0%,#e4d6cc 40%,#f5f5f5 70%,#dcdcdc 100%)}
.photo-child{top:1356px;left:600px;width:600px;height:435px;background:linear-gradient(110deg,#ddd6cc 0%,#efe9e2 45%,#f1c6cf 70%,#e9e2da 100%)}

.next{top:2098px;left:79px;width:1000px}
.next h3{font-size:31px;font-weight:700;margin-bottom:14px}
.next p{font-size:14px;line-height:26px;color:#444}

.more-title{top:2278px;left:0;width:1300px;text-align:center;color:var(--teal);font-size:31px;font-weight:700}
.buttons{top:2347px;left:77px;width:1047px;height:105px;display:flex}
.buttons div{flex:1;display:flex;align-items:center;justify-content:center;font-size:31px;font-weight:400}
.btn-teal{background:var(--teal);color:var(--white)}
.btn-yellow{background:var(--yellow);color:#333}

.brands{top:2520px;left:79px;width:1042px;display:flex}
.brands div{flex:1;text-align:center;font-size:24px;font-weight:600;color:#222;letter-spacing:1px}
.frames{top:2612px;left:79px;width:1042px;display:flex}
.frames div{flex:1;display:flex;justify-content:center}
.frame{width:118px;height:56px;border-radius:28px}

/* footer */
.footer{top:2750px;left:0;width:1200px;height:408px;background:var(--yellow)}
.fcol{position:absolute;top:2812px}
.fcol h4{color:var(--teal);font-size:21px;font-weight:600;margin-bottom:22px}
.frow{display:flex;gap:18px;font-size:14px;line-height:26px;color:#333;margin-bottom:16px;align-items:flex-start}
.frow svg{flex:none;margin-top:4px}
.hours p{font-size:14px;line-height:31px;color:#333}
.hours b{font-weight:700}
.dir{position:absolute;top:3063px;width:280px;height:42px;border-radius:21px;background:var(--dark-btn);color:var(--white);font-size:15px;display:flex;align-items:center;padding-left:18px;gap:20px}
.fsocial{position:absolute;top:3064px;display:flex;gap:10px;left:789px}
.fsocial div{width:42px;height:42px;border-radius:50%;background:var(--dark-btn)}
.fsocial div:first-child{background:var(--teal)}
.copy{top:3158px;left:0;width:1200px;height:71px;background:var(--yellow);border-top:1px solid rgba(0,0,0,.06);display:flex;align-items:center;justify-content:center;font-size:14px;color:#666}
.copy b{color:var(--teal);font-weight:700;margin:0 4px}
</style>
</head>
<body>

<div class="abs topbar">
  <div class="cell" style="left:463px;width:171px">
    <svg width="20" height="20" viewBox="0 0 24 24" fill="none" stroke="#fbe564" stroke-width="2"><path d="M22 16.9v3a2 2 0 0 1-2.2 2 19.8 19.8 0 0 1-8.6-3.1 19.5 19.5 0 0 1-6-6A19.8 19.8 0 0 1 2.1 4.2 2 2 0 0 1 4.1 2h3a2 2 0 0 1 2 1.7c.1 1 .4 1.9.7 2.8a2 2 0 0 1-.5 2.1L8 9.9a16 16 0 0 0 6 6l1.3-1.3a2 2 0 0 1 2.1-.4c.9.3 1.8.6 2.8.7a2 2 0 0 1 1.7 2z"/></svg>
    555-210-4410
  </div>
  <div class="cell" style="left:634px;width:281px">
    <svg width="20" height="16" viewBox="0 0 24 18" fill="none" stroke="#fbe564" stroke-width="2"><rect x="1" y="1" width="22" height="16"/><path d="M1 1l11 9 11-9"/></svg>
    info@lumoraoptometry.com
  </div>
  <div class="cell social" style="left:915px"><span class="dot"></span></div>
  <div class="cell social" style="left:967px"><span class="dot"></span></div>
  <div class="cell social" style="left:1019px"><span class="dot"></span></div>
  <div class="cell social" style="left:1071px;border-right:1px solid rgba(255,255,255,.25)"><span class="dot"></span></div>
</div>

<div class="abs logo-box">
  <div class="sq"></div>
  <div class="name">LUMORA<br>OPTOMETRY</div>
</div>

<nav class="abs nav">
  <span class="home">Home</span><span>Our Team</span><span>Eye Care</span><span class="active">Myopia Control Clinic</span><span>Eyewear</span><span>Blog</span><span>Contact Us</span>
</nav>
<svg class="abs search" width="22" height="22" viewBox="0 0 24 24" fill="none" stroke="#1691b3" stroke-width="2"><circle cx="10" cy="10" r="7"/><path d="M15 15l7 7"/></svg>

<header class="abs title-band"><h1>MYOPIA CONTROL CLINIC</h1></header>

<section class="abs intro">
  <h2>What is Orthokeratology (OrthoK)?</h2>
  <p>Dr. Venn is excited to offer a nonsurgical procedure using specially designed contact lenses to gently reshape the curvature of the eye to improve vision while you sleep. It works each night while you sleep for eight hours. You put the lenses on when you go to bed and remove them when you wake up. Your vision is clear during the day, without glasses or daytime contact lenses. Now you can enjoy your days with clear vision at school, work, and playing sports without the hassle of glasses or contact lenses drying out your eyes during the day.</p>
  <p><strong>Understanding OrthoK</strong> Our eyes must be in focus for us to see clearly, just as a camera must be in focus to obtain a sharp photo. Light, which gives us vision, is focused largely by the eye's front surface or cornea. OrthoK gently molds or focuses the cornea while a person is sleeping, creating a sharpened image when they wake. Dr. Venn will design the OrthoK mold to obtain the change needed to achieve clearly focused vision. When the lens is removed in the morning the cornea begins to return to its original shape but so slowly that good vision is maintained all waking hours. Each night the process is repeated although some find they only need to wear their molds every other night, depending on prescription. The elastic tissue of the eye is not harmed by this daily process. OrthoK is safe and reversible. It is not a permanent alteration of tissue and thus is an excellent Lasik alternative for those reluctant or unable to undergo a surgical alteration of their corneas.</p>
</section>

<div class="abs photo-optician" role="img" aria-label="Photo of a woman's face beside an eye chart, with a focus frame over one eye"></div>

<div class="tile teal" style="top:825px;left:600px;width:600px;height:218px;padding:44px 40px 0 42px">
  <h3>Who is a Candidate?</h3>
  <p>The majority of nearsighted (myopic) individuals with healthy eyes can benefit from OrthoK, from children as young as seven years to adults in their 50s.</p>
</div>

<div class="tile yellow" style="top:1043px;left:600px;width:600px;height:313px;padding:44px 76px 0 42px">
  <h3>Will My Prescription Work?</h3>
  <p>OrthoK treats myopia (nearsightedness), the condition where distance vision is blurred. Prescription powers up to about -7.00 are generally treatable. Astigmatism, a common optical condition where vision is distorted due to uneven curvatures of the eye surfaces, is treatable in low to moderate amounts. Some doctors using specialized OrthoK lenses routinely exceed these levels for many patients with great success.</p>
</div>

<div class="tile teal" style="top:1356px;left:0;width:600px;height:435px;padding:40px 40px 0 79px">
  <h3>Can my child have OrthoK?</h3>
  <p>Patients as young as seven years old are excellent candidates and we make the decision based on their maturity, hygiene and motivation. These students are able to play, swim, participate in sports and other healthy activities without the problems of glasses or daytime contact lens wear. Perhaps the most exciting candidate for OrthoK is the young patient who has become nearsighted for the first time when there is a strong family history of nearsightedness progressing rapidly during childhood. The child whose nearsightedness has been proven to already be progressing is another excellent candidate. There is growing evidence that OrthoK can stop this progression.</p>
</div>

<div class="abs photo-child" role="img" aria-label="Photo of a smiling young girl wearing glasses, leaning on an open book"></div>

<div class="tile yellow" style="top:1791px;left:0;width:1200px;height:262px;padding:52px 90px 0 79px">
  <h3>Am I too old for OrthoK?</h3>
  <p style="color:#444">Probably not! Patients over forty years old will generally need to consider the fact that near reading vision may be blurred, the same thing that happens to everyone with good distance vision as they get older. This condition (presbyopia) can be treated by modifying the power of OrthoK lenses, wearing reading glasses or other options that can be discussed with your doctor. Many patients in their sixties and seventies are wearing OrthoK lenses successfully.</p>
</div>

<section class="abs next">
  <h3>What do I do next?</h3>
  <p>The next step is visit Lumora Optometry for a free consultation and we will let you know based on your prescription if you are a good candidate for OrthoK.</p>
</section>

<h3 class="abs more-title">For Additional Information Click Here:</h3>
<div class="abs buttons">
  <div class="btn-teal">ClariLens</div>
  <div class="btn-yellow">Vision Library</div>
  <div class="btn-teal">Learn More</div>
</div>

<div class="abs brands">
  <div>MARLO</div><div>ALDEN REY</div><div>SORELLE &amp; CO.</div><div>VELOCA</div><div>OSTRELLE</div><div>KESTRIN</div>
</div>
<div class="abs frames">
  <div><div class="frame" role="img" aria-label="Product image of blue-tinted sunglasses" style="background:linear-gradient(90deg,#5d7590,#8fa6c0)"></div></div>
  <div><div class="frame" role="img" aria-label="Product image of tortoiseshell round glasses" style="background:linear-gradient(90deg,#5a3b26,#a07350)"></div></div>
  <div><div class="frame" role="img" aria-label="Product image of brown gradient round sunglasses" style="background:linear-gradient(90deg,#a27e6e,#e0cfc6)"></div></div>
  <div><div class="frame" role="img" aria-label="Product image of thin gold wire glasses" style="background:linear-gradient(90deg,#eadfc8,#f6f0e4)"></div></div>
  <div><div class="frame" role="img" aria-label="Product image of black frame glasses" style="background:linear-gradient(90deg,#2a2a2a,#6a6a6a)"></div></div>
  <div><div class="frame" role="img" aria-label="Product image of clear frame sunglasses with amber lenses" style="background:linear-gradient(90deg,#c9a98c,#e8e4e0)"></div></div>
</div>

<footer class="abs footer"></footer>

<div class="fcol" style="left:79px;width:260px">
  <h4>Lumora Optometry</h4>
  <div class="frow"><svg width="22" height="20" viewBox="0 0 24 24" fill="#1691b3"><path d="M22 16.9v3a2 2 0 0 1-2.2 2 19.8 19.8 0 0 1-8.6-3.1 19.5 19.5 0 0 1-6-6A19.8 19.8 0 0 1 2.1 4.2 2 2 0 0 1 4.1 2h3a2 2 0 0 1 2 1.7c.1 1 .4 1.9.7 2.8a2 2 0 0 1-.5 2.1L8 9.9a16 16 0 0 0 6 6l1.3-1.3a2 2 0 0 1 2.1-.4c.9.3 1.8.6 2.8.7a2 2 0 0 1 1.7 2z"/></svg>555-210-4410</div>
  <div class="frow"><svg width="22" height="20" viewBox="0 0 24 22" fill="#1691b3"><rect x="6" y="1" width="12" height="7"/><rect x="1" y="8" width="22" height="11" rx="2"/><rect x="6" y="14" width="12" height="7" fill="#fbe564" stroke="#1691b3" stroke-width="2"/></svg>555-210-4470</div>
  <div class="frow"><svg width="22" height="16" viewBox="0 0 24 18" fill="#1691b3"><rect x="1" y="1" width="22" height="16" rx="1"/><path d="M1 2l11 8 11-8" stroke="#fbe564" stroke-width="2" fill="none"/></svg>info@brivaloka.com</div>
  <div class="frow"><svg width="22" height="22" viewBox="0 0 24 24" fill="#1691b3"><path d="M12 1a8 8 0 0 0-8 8c0 6 8 14 8 14s8-8 8-14a8 8 0 0 0-8-8z"/><circle cx="12" cy="9" r="3" fill="#fbe564"/></svg>4410 Arden Lane, Westbrook,<br>CA 90210</div>
</div>
<div class="dir" style="left:77px">Get directions on the map <svg width="32" height="10" viewBox="0 0 32 10" fill="none" stroke="#1691b3" stroke-width="2"><path d="M0 5h30M25 1l5 4-5 4"/></svg></div>

<div class="fcol" style="left:435px;width:260px">
  <h4>North Hills</h4>
  <div class="frow"><svg width="22" height="20" viewBox="0 0 24 24" fill="#1691b3"><path d="M22 16.9v3a2 2 0 0 1-2.2 2 19.8 19.8 0 0 1-8.6-3.1 19.5 19.5 0 0 1-6-6A19.8 19.8 0 0 1 2.1 4.2 2 2 0 0 1 4.1 2h3a2 2 0 0 1 2 1.7c.1 1 .4 1.9.7 2.8a2 2 0 0 1-.5 2.1L8 9.9a16 16 0 0 0 6 6l1.3-1.3a2 2 0 0 1 2.1-.4c.9.3 1.8.6 2.8.7a2 2 0 0 1 1.7 2z"/></svg>555-318-6020</div>
  <div class="frow"><svg width="22" height="16" viewBox="0 0 24 18" fill="#1691b3"><rect x="1" y="1" width="22" height="16" rx="1"/><path d="M1 2l11 8 11-8" stroke="#fbe564" stroke-width="2" fill="none"/></svg>northhills@brivaloka.com</div>
  <div class="frow"><svg width="22" height="22" viewBox="0 0 24 24" fill="#1691b3"><path d="M12 1a8 8 0 0 0-8 8c0 6 8 14 8 14s8-8 8-14a8 8 0 0 0-8-8z"/><circle cx="12" cy="9" r="3" fill="#fbe564"/></svg>2280 Larkmoor St.,Suite 4,<br>North Hills, CA 90215</div>
</div>
<div class="dir" style="left:433px">Get directions on the map <svg width="32" height="10" viewBox="0 0 32 10" fill="none" stroke="#1691b3" stroke-width="2"><path d="M0 5h30M25 1l5 4-5 4"/></svg></div>

<div class="fcol hours" style="left:791px;width:260px">
  <h4>Opening Hours</h4>
  <p>Monday - Thursday : <b>9 am - 6 pm</b></p>
  <p>Friday : <b>8.30 am - 5 pm</b></p>
  <p>Saturday &nbsp;: <b>8.30 am- 5 pm</b></p>
  <p>Closed on <b>Sundays</b></p>
  <p style="line-height:21px;margin-top:5px">Please keep in mind we are closed<br>for <b>lunch 1-2 pm</b></p>
</div>
<div class="fsocial"><div></div><div></div><div></div><div></div></div>

<div class="abs copy">Copyright © <b>LUMORA OPTOMETRY</b> - 2019 . All right Reserved</div>

</body>
</html>
```